Business card design for my company.
I would like the card's background colour to be black. You can also see our web site to get an idea of our brand. https://www.tmwhomecrafting.com.au/
- Name
- Email

```html
<!DOCTYPE html>
<html lang="en">
<head>
<meta charset="utf-8">
<title>TMW Home Crafting – Business Card</title>
<link href="https://fonts.googleapis.com/css2?family=Arimo:wght@400;700&display=swap" rel="stylesheet">
<style>
  :root {
    --backdrop: #e4e4e4;
    --card-dark: #313131;
    --brand-green: #0b9446;
    --back-green: #0b9645;
    --deep-green: #067a36;
    --paper-white: #f4f4f4;
    --rule-grey: #8a8a8a;
  }
  * { box-sizing: border-box; margin: 0; padding: 0; }
  html, body {
    width: 1200px; height: 1200px; overflow: hidden;
    background: var(--backdrop);
    font-family: "Arimo", Arial, sans-serif;
  }
  .card {
    position: absolute; left: 256px; width: 688px; height: 393px;
    overflow: hidden;
  }
  .card-front { top: 150px; background: var(--card-dark); color: var(--paper-white); }
  .card-back { top: 655px; background: var(--back-green); }

  .brand-mark {
    position: absolute; right: 45px; top: 88px;
    display: flex; align-items: center; gap: 12px;
  }
  .brand-square { width: 18px; height: 18px; background: var(--brand-green); }
  .brand-name {
    font-weight: 700; font-size: 30px; letter-spacing: 1px;
    color: var(--paper-white);
  }

  .holder-name {
    position: absolute; left: 48px; top: 215px;
    font-size: 27px; font-weight: 700; color: var(--brand-green); letter-spacing: .3px;
  }
  .holder-role {
    position: absolute; left: 48px; top: 248px; font-size: 15px;
  }
  .divider {
    position: absolute; left: 48px; top: 275px; width: 595px; height: 1px;
    background: var(--rule-grey);
  }
  .contact-list {
    position: absolute; left: 42px; top: 285px; list-style: none;
  }
  .contact-list li {
    display: flex; align-items: center; height: 20.5px; font-size: 16px;
  }
  .contact-icon { width: 16px; height: 16px; margin-right: 12px; fill: var(--brand-green); }
  .address {
    position: absolute; right: 41px; top: 288px;
    text-align: right; font-size: 16px; line-height: 21px; font-style: normal;
  }
  .footer-band { position: absolute; left: 0; bottom: 0; width: 688px; height: 31px; }
  .web-address {
    position: absolute; right: 41px; bottom: 7px; font-size: 14.5px; line-height: 17px;
    color: var(--paper-white);
  }

  .back-brand {
    position: absolute; inset: 0;
    display: flex; align-items: center; justify-content: center; gap: 16px;
  }
  .back-brand .brand-square { width: 26px; height: 26px; background: var(--deep-green); }
  .back-brand .brand-name { font-size: 40px; color: var(--deep-green); letter-spacing: 2px; }
</style>
</head>
<body>
  <section class="card card-front">
    <div class="brand-mark">
      <span class="brand-square"></span>
      <span class="brand-name">TMW HOME CRAFTING</span>
    </div>

    <h1 class="holder-name">LIAM HARPER</h1>
    <p class="holder-role">President</p>
    <div class="divider"></div>

    <ul class="contact-list">
      <li>
        <svg class="contact-icon" viewBox="0 0 24 24"><path d="M6.6 10.8a15 15 0 0 0 6.6 6.6l2.2-2.2c.3-.3.7-.4 1-.2 1.1.4 2.3.6 3.6.6.6 0 1 .4 1 1V20c0 .6-.4 1-1 1A17 17 0 0 1 3 4c0-.6.4-1 1-1h3.5c.6 0 1 .4 1 1 0 1.3.2 2.5.6 3.6.1.3 0 .7-.2 1z"/></svg>
        555-210-4187
      </li>
      <li>
        <svg class="contact-icon" viewBox="0 0 24 24"><path d="M7 1h10a2 2 0 0 1 2 2v18a2 2 0 0 1-2 2H7a2 2 0 0 1-2-2V3a2 2 0 0 1 2-2zm0 3v14h10V4zm5 15.5a1 1 0 1 0 0 2 1 1 0 0 0 0-2z"/></svg>
        555-382-9061
      </li>
      <li>
        <svg class="contact-icon" viewBox="0 0 24 24"><path d="M2 5h20v14H2zm2 2v.5l8 5 8-5V7zm0 2.8V17h16V9.8l-8 5z"/></svg>
        info@tmwhomecrafting.com.au
      </li>
    </ul>

    <address class="address">
      412 Wattle Grove Road<br>
      Ballarat, Victoria 3350
    </address>

    <svg class="footer-band" viewBox="0 0 688 31" preserveAspectRatio="none">
      <rect x="0" y="19" width="688" height="12" fill="var(--brand-green)"/>
      <path d="M0 3 H412 L406 14 Q404 15 402 15 H0 Z" fill="var(--paper-white)"/>
      <path d="M420 0 H688 V19 H408 L414 4 Q415 0 420 0 Z" fill="var(--brand-green)"/>
    </svg>
    <span class="web-address">www.tmwhomecrafting.com.au</span>
  </section>

  <section class="card card-back">
    <div class="back-brand">
      <span class="brand-square"></span>
      <span class="brand-name">TMW HOME CRAFTING</span>
    </div>
  </section>
</body>
</html>
```